Business card for my new company (Accounting firm)

I need a business card for my new business Brightwell Advisory and Ledger SA. Our services are accounting, tax, audit and financial management. Our customers are small companies, start-ups and new companies. The final design has to show financial security, trust and growth. Please find our logo attached to the business card. Text for the business card: Brightwell Advisory and Ledger SA Tomas Varenholt Director and Founder Certified Accountant Tel. 022 418 57 34 tv@clairevalconseil.ch www.clairevalconseil.ch Rue des Vergières 27 1201 Geneva
Target Market(s)
Our customers are small companies, start-ups and new companies.
Industry/Entity Type
Finance And Accounting
Contact Information for Business Card
Claireval Conseil et Comptes SA
Tomas Varenholt
Directeur et Fondateur
Expert-comptable diplômé
Tél. 022 418 57 34
tv@clairevalconseil.ch
www.clairevalconseil.ch
Rue des Vergières 27
1201 Genève

```html
<!DOCTYPE html>
<html lang="en">
<head>
<meta charset="utf-8">
<title>Claireval Conseil et Comptes SA — Business Card</title>
<link rel="stylesheet" href="https://fonts.googleapis.com/css2?family=Lato:wght@400;700&family=Montserrat:wght@500&display=swap">
<style>
  :root {
    --backdrop: #3a332f;
    --card: #121212;
    --card-edge: #1c1c1c;
    --accent: #2aa3e0;
    --text: #c6c6c6;
    --divider: #262626;
    --silver: #d9d9d9;
  }
  * { box-sizing: border-box; margin: 0; padding: 0; }
  html, body { width: 1200px; height: 844px; overflow: hidden; }
  body {
    background: var(--backdrop);
    font-family: "Lato", Arial, sans-serif;
    position: relative;
  }
  .card {
    position: absolute;
    top: 267px;
    width: 520px;
    height: 310px;
    background: var(--card);
    border: 1px solid var(--card-edge);
    border-radius: 3px;
    box-shadow: 0 10px 30px rgba(0,0,0,.45);
  }
  .card--front { left: 50px; }
  .card--back { left: 630px; display: flex; align-items: center; justify-content: center; }

  .brand {
    position: absolute;
    left: 0; top: 0;
    width: 240px; height: 310px;
    display: flex; flex-direction: column; align-items: center; justify-content: center;
    gap: 8px;
  }
  .brand__mark {
    width: 18px; height: 18px; background: var(--accent);
  }
  .brand__name {
    font-family: "Montserrat", Arial, sans-serif;
    font-weight: 500;
    color: var(--text);
    font-size: 15px;
    letter-spacing: 2px;
    text-transform: uppercase;
    text-align: center;
    line-height: 1.5;
  }
  .divider {
    position: absolute;
    left: 245px; top: 34px;
    width: 1px; height: 242px;
    background: var(--divider);
  }
  .contact {
    position: absolute;
    left: 272px; top: 58px;
    color: var(--text);
    font-size: 15px;
    line-height: 1.3;
  }
  .contact__name {
    color: var(--accent);
    font-weight: 700;
    font-size: 17px;
    text-transform: uppercase;
    letter-spacing: .3px;
  }
  .contact__roles { margin-bottom: 10px; }
  .contact__list { list-style: none; margin-bottom: 12px; }
  .contact__list li { display: flex; align-items: center; gap: 8px; }
  .contact__list svg { width: 11px; height: 11px; fill: var(--accent); flex: none; }

  .back__name {
    font-family: "Montserrat", Arial, sans-serif;
    font-weight: 500;
    color: var(--silver);
    font-size: 26px;
    letter-spacing: 4px;
    text-transform: uppercase;
  }
</style>
</head>
<body>
  <section class="card card--front">
    <div class="brand">
      <span class="brand__mark"></span>
      <p class="brand__name">Claireval<br>Conseil et Comptes</p>
    </div>
    <span class="divider"></span>
    <div class="contact">
      <p class="contact__name">SA Tomas Varenholt</p>
      <p class="contact__roles">Director and Founder<br>Certified Accountant</p>
      <ul class="contact__list">
        <li><svg viewBox="0 0 12 12" aria-hidden="true"><path d="M1 3c0-1 1-2 2-2h6c1 0 2 1 2 2v1H8V3H4v1H1zM2 5h8l1 5H1z"/></svg>022 418 57 34</li>
        <li><svg viewBox="0 0 12 12" aria-hidden="true"><path d="M1 2h10v1L6 6 1 3zM1 4.5l5 3 5-3V10H1z"/></svg>tv@clairevalconseil.ch</li>
        <li><svg viewBox="0 0 12 12" aria-hidden="true"><circle cx="6" cy="6" r="5"/></svg>www.clairevalconseil.ch</li>
      </ul>
      <address style="font-style:normal">Rue des Vergières 27<br>1201 Geneva</address>
    </div>
  </section>

  <section class="card card--back">
    <p class="back__name">Claireval</p>
  </section>
</body>
</html>
```